Clear sticker design for packaging

I need 4” diameter clear stickers designed for birthdays, thank you , teachers day and all the other special days to complete my gift packaging. They will go on the top of each tube to differentiate each gift for each occasion. Our design is on craft paper and I’ve uploaded a few examples of what we are trying to achieve. Last picture is the top of our tube where the stickers will be placed. We don’t want too much color unless for Christmas and Valentine’s Day maybe! We are working with black and gold or a mixture of both mostly

```html
<!DOCTYPE html>
<html lang="en">
<head>
<meta charset="utf-8">
<title>Occasion Stickers</title>
<link href="https://fonts.googleapis.com/css2?family=Dancing+Script:wght@700&family=Montserrat:wght@400&display=swap" rel="stylesheet">
<style>
  :root {
    --bg-top: #5f5f5f;
    --bg-bottom: #8e8e8e;
    --sticker: #e6dccf;
    --sticker-shade: #cfc4b6;
    --ink: #231f20;
    --shadow: rgba(0, 0, 0, 0.28);
  }
  * { margin: 0; padding: 0; box-sizing: border-box; }
  html, body {
    width: 1200px;
    height: 959px;
    overflow: hidden;
  }
  body {
    position: relative;
    background: linear-gradient(180deg, var(--bg-top) 0%, var(--bg-bottom) 100%);
  }
  .sticker {
    position: absolute;
    width: 300px;
    height: 300px;
    border-radius: 50%;
    background: var(--sticker);
    box-shadow: 0 4px 10px var(--shadow);
    overflow: hidden;
  }
  .sticker--birthday { left: 260px; top: 110px; }
  .sticker--teachers { left: 640px; top: 110px; }
  .sticker--thanks   { left: 450px; top: 500px; }

  .sticker__burst {
    position: absolute;
    inset: 0;
    border-radius: 50%;
    background: radial-gradient(circle at 50% 50%, var(--sticker) 0%, var(--sticker) 32%, var(--sticker-shade) 70%, var(--sticker) 100%);
  }
  .sticker__text {
    position: absolute;
    inset: 0;
    display: flex;
    flex-direction: column;
    align-items: center;
    justify-content: center;
    color: var(--ink);
    text-align: center;
  }
  .sticker__lead {
    font-family: "Montserrat", sans-serif;
    font-weight: 400;
    font-size: 16px;
    letter-spacing: 1.5px;
    line-height: 1.15;
    margin-bottom: 2px;
  }
  .sticker__script {
    font-family: "Dancing Script", cursive;
    font-weight: 700;
    font-size: 60px;
    line-height: 1;
    white-space: nowrap;
  }
  .sticker--teachers .sticker__script { font-size: 46px; }
  .sticker--thanks .sticker__lead { font-size: 14px; margin-bottom: 2px; }
  .sticker--thanks .sticker__script { font-size: 62px; }
</style>
</head>
<body>

<div class="sticker sticker--birthday">
  <div class="sticker__burst" role="img" aria-label="Decorative sunburst ray ornament with small stars"></div>
  <div class="sticker__text">
    <span class="sticker__lead">HAPPY</span>
    <span class="sticker__script">Birthday!</span>
  </div>
</div>

<div class="sticker sticker--teachers">
  <div class="sticker__burst" role="img" aria-label="Decorative sunburst ray ornament with small stars"></div>
  <div class="sticker__text">
    <span class="sticker__lead">HAPPY</span>
    <span class="sticker__script">Teachers day!</span>
  </div>
</div>

<div class="sticker sticker--thanks">
  <div class="sticker__burst" role="img" aria-label="Decorative sunburst ray ornament with small stars"></div>
  <div class="sticker__text">
    <span class="sticker__lead">A<br>SWEET</span>
    <span class="sticker__script">Thank you</span>
  </div>
</div>

</body>
</html>
```